Chimney Service company needs new business card design

We need a updated business card with our new logo added. We provide a full range of chimney services throughout Vermont and New Hampshire. The business card will be one sided and color. Attached is our current business card another document showing all the information we would like on the card.
We dont like a lot of flashy colors.... here is a link to our website to get an idea of our branding www.flueguardianvt.example

Target Market(s)

homeowners

Industry/Entity Type

Business

Contact Information for Business Card

See attached sheet for content.

Font styles to use
Serif
Sans Serif

Requirements
Must have
• all information provided on separate sheet
Should not have
• Additional information that may clogg up design

```html
<!DOCTYPE html>
<html lang="en">
<head>
<meta charset="utf-8">
<title>Flue Guardian – Business Card</title>
<link rel="stylesheet" href="https://fonts.googleapis.com/css2?family=Cinzel:wght@500&family=Archivo:wght@700&family=Open+Sans:wght@400;600&display=swap">
<style>
  :root {
    --brand-red: #8c0a0a;
    --charcoal: #2f2f2f;
    --ink: #333333;
    --card-light: #f5f5f5;
    --card-shade: #e4e4e4;
    --backdrop: #b9b9b9;
    --rule: #9a1414;
  }
  * { margin: 0; padding: 0; box-sizing: border-box; }
  html, body { width: 1200px; height: 576px; overflow: hidden; background: var(--backdrop); }
  .canvas { position: relative; width: 1200px; height: 576px; font-family: "Open Sans", sans-serif; color: var(--ink); }

  .card {
    position: absolute; border-radius: 13px; overflow: hidden;
    background: linear-gradient(160deg, var(--card-light), var(--card-shade));
  }
  .card--front { left: 82px; top: 138px; width: 484px; height: 294px; }
  .card--back  { left: 602px; top: 138px; width: 480px; height: 290px; }

  .front-header { position: absolute; left: 0; top: 0; width: 484px; height: 140px; }

  .brand { position: absolute; display: flex; align-items: center; gap: 12px; }
  .brand__square { width: 16px; height: 16px; flex: none; }
  .brand__name { font-family: "Cinzel", serif; font-weight: 500; white-space: nowrap; letter-spacing: 0.5px; }
  .brand--front { left: 0; right: 0; top: 40px; justify-content: center; }
  .brand--front .brand__square { background: #fff; }
  .brand--front .brand__name { color: #fff; font-size: 27px; }

  .services { position: absolute; left: 8px; right: 8px; top: 160px; display: flex; justify-content: space-between; }
  .service { flex: 1; display: flex; flex-direction: column; align-items: center; position: relative; }
  .service + .service::before {
    content: ""; position: absolute; left: 0; top: 10px; height: 68px; width: 1px; background: var(--rule); opacity: 0.7;
  }
  .service__icon { width: 40px; height: 48px; border-radius: 3px; background: linear-gradient(180deg, #b33a3a, var(--brand-red)); opacity: 0.85; }
  .service__label { margin-top: 12px; font-size: 11.5px; line-height: 14px; text-align: center; color: var(--ink); }

  .footer-rule { position: absolute; display: flex; align-items: center; gap: 10px; font-size: 11.5px; white-space: nowrap; }
  .footer-rule .line { height: 1.5px; background: var(--rule); }
  .front-footer { left: 0; right: 0; top: 268px; justify-content: center; }
  .front-footer .line { width: 94px; }
  .web-accent { color: var(--brand-red); }

  .brand--back { left: 36px; top: 172px; }
  .brand--back .brand__square { background: var(--brand-red); }
  .brand--back .brand__name { color: var(--charcoal); font-size: 22px; }

  .service-area { position: absolute; left: 263px; top: 64px; width: 200px; text-align: center; }
  .service-area__title { font-family: "Archivo", sans-serif; font-weight: 700; font-size: 18px; line-height: 22px; color: var(--charcoal); letter-spacing: 0.3px; }
  .service-area__since { margin-top: 4px; display: flex; align-items: center; gap: 6px; justify-content: center; font-size: 8.5px; }
  .service-area__since .line { width: 48px; height: 1.5px; background: var(--rule); }

  .contacts { position: absolute; left: 268px; top: 150px; list-style: none; }
  .contact { display: flex; align-items: center; gap: 9px; height: 19.5px; font-size: 11.5px; }
  .contact svg { width: 10px; height: 10px; fill: var(--brand-red); flex: none; }

  .back-footer { left: 19px; top: 264px; gap: 12px; }
  .back-footer .line { width: 50px; }
  .back-footer .divider { color: var(--brand-red); margin: 0 6px; }
</style>
</head>
<body>
<div class="canvas">

  <section class="card card--front">
    <svg class="front-header" viewBox="0 0 484 140" aria-hidden="true">
      <path d="M0 98 Q250 172 484 112 V132 Q250 176 0 104 Z" fill="var(--charcoal)"/>
      <path d="M0 0 H484 V100 Q250 162 0 96 Z" fill="var(--brand-red)"/>
    </svg>
    <div class="brand brand--front">
      <span class="brand__square"></span>
      <span class="brand__name">FLUE GUARDIAN</span>
    </div>

    <div class="services">
      <div class="service">
        <div class="service__icon" role="img" aria-label="Icon of a masonry chimney"></div>
        <p class="service__label">Full Masonry<br>Services</p>
      </div>
      <div class="service">
        <div class="service__icon" role="img" aria-label="Icon of bricks being restored"></div>
        <p class="service__label">Historic Chimney<br>Restoration</p>
      </div>
      <div class="service">
        <div class="service__icon" role="img" aria-label="Icon of a stainless steel liner"></div>
        <p class="service__label">Stainless<br>Steel Liners</p>
      </div>
      <div class="service">
        <div class="service__icon" role="img" aria-label="Icon of bricks and a trowel"></div>
        <p class="service__label">New Chimney<br>Installations</p>
      </div>
      <div class="service">
        <div class="service__icon" role="img" aria-label="Icon of a chimney sweep brush"></div>
        <p class="service__label">Fully Certified<br>Chimney sweeps</p>
      </div>
    </div>

    <div class="footer-rule front-footer">
      <span class="line"></span>
      <span>www.<span class="web-accent">flueguardianvt</span>.example</span>
      <span class="line"></span>
    </div>
  </section>

  <section class="card card--back">
    <div class="brand brand--back">
      <span class="brand__square"></span>
      <span class="brand__name">FLUE GUARDIAN</span>
    </div>

    <div class="service-area">
      <h2 class="service-area__title">SERVING VT AND<br>NEW HAMPSHIRE</h2>
      <div class="service-area__since"><span class="line"></span><span>SINCE 1989</span><span class="line"></span></div>
    </div>

    <ul class="contacts">
      <li class="contact">
        <svg viewBox="0 0 10 10" aria-hidden="true"><path d="M1 3 Q5 0 9 3 L8 4.5 L6.5 3.8 L6.5 3 Q5 2.5 3.5 3 L3.5 3.8 L2 4.5 Z M2.5 5 H7.5 L8.5 9 H1.5 Z"/></svg>
        <span>802-555-0147</span>
      </li>
      <li class="contact">
        <svg viewBox="0 0 10 10" aria-hidden="true"><path d="M0.5 2 H9.5 V8 H0.5 Z M1 2.5 L5 5.5 L9 2.5" stroke="#fff" stroke-width="0.8"/></svg>
        <span>info@flueguardianvt.example</span>
      </li>
      <li class="contact">
        <svg viewBox="0 0 10 10" aria-hidden="true"><circle cx="5" cy="5" r="4.5"/><path d="M0.5 5 H9.5 M5 0.5 V9.5 M5 0.5 Q2 5 5 9.5 M5 0.5 Q8 5 5 9.5" stroke="#fff" stroke-width="0.6" fill="none"/></svg>
        <span>www.<span class="web-accent">flueguardianvt</span>.example</span>
      </li>
    </ul>

    <div class="footer-rule back-footer">
      <span class="line"></span>
      <span>Fully Insured – Free Estimates<span class="divider">|</span>Family Owned &amp; Operated</span>
      <span class="line"></span>
    </div>
  </section>

</div>
</body>
</html>
```